Stationery Design Project

We need a stationery design for our Norwegian trucking company. We have existed for about 15 years and our 12 drivers uses relatively new vehicles to transport goods around in northern Norway. Long distance routes with fresh fish og food transport is our main operations.

We have already made alogo that's printed on our trucks. The logo and a picture of our trucks is attached. I think the logo i crappy, but since its already in use, changing it is not an option in this round. Still using a better colour scheme in the overall stationery and more interesting fonts is possible (altso in the logo).

Company details:
Name: Kjelvraket AS
Organisation nr 873 615 309
Post adress: 8642 Raudvik

I like minimalism and simplicity. I am avalibly for questions in normal GMT working hours either here or on mail: ivar@fjordlast.no

Reason: Hi. Im extending the deadline because I needed some time to find a vector file of our logo. Sorry for the inconvenience

Hi, and thanks for all your interest in the project. Some updates:

-          I have decided to commit to using one of the designs. Some designer will get the payment.

-          I have extended the deadline with 24 hours since I needed some time to find our firms vector logo (a slow Swedish man was holding me up)

-          We will not choose a design before the deadline. No need to rush.

-          We have received a lot of great design and think there is a need to specified the product we want to make:

o   Business Card for all our employers. I just need the design and will duplicate with the correct numbers and name myself. The information on should be: Logo, employer’s name, Phone number, email, website, Postal number and address. Use this as a template: logo, Leif Brattvoll, 47382066, Leif@fjordlast.no,, fjordlast.no, 8642 Raudvik. The order and placement of the information is your creative decision.

o   Stickers to put on the goods we travel. On the sticker the should be the following information: Logo, phone number, Tekst and link: Fraktæ av Kjelvraket. Ke du syns? Fjordlast.no/tilbakemelding (this means: Handled by Kjelvraket. What do you think Fjordlast.no/feedback -à the link will be a feedback form). The placement the information and size is your creative decision with some stings: we have been thinking of using Drukko for printing and see that a size about 6x6 cm, 8x5 or something like that. (with 3000 copies our budget is 200 punds). Any suggestions of other suppliers are welcome. Drukko price calculator http://www.drukkolabelhouse.co.uk/digital-litho-printing/printing-labels-tags/stickers/

o   Letterhead with logo, address, phone number and organizational number.

o   Envelopes with logo,address, phone number and organizational number.

Have a nice day.

 

 

• Using the blue colour in the logo and using a similar graphic approch.

```html
<!DOCTYPE html>
<html lang="no">
<head>
<meta charset="utf-8">
<title>Kjelvraket – visittkort</title>
<link rel="stylesheet" href="https://fonts.googleapis.com/css2?family=Open+Sans:wght@400;600;700&display=swap">
<style>
  :root {
    --backdrop: #d6d8db;
    --navy: #0b4fa3;
    --sky: #0b74bd;
    --brand: #1d64b4;
    --stripe: #2a86d1;
    --ink: #2b2b2b;
    --paper: #ffffff;
    --edge: #3a3a3a;
  }
  * { margin: 0; padding: 0; box-sizing: border-box; }
  html, body { width: 1200px; height: 751px; overflow: hidden; }
  body {
    position: relative;
    background: var(--backdrop);
    font-family: "Open Sans", Arial, sans-serif;
    color: var(--ink);
  }
  .card {
    position: absolute;
    border-radius: 18px;
    overflow: hidden;
  }
  .card--front { left: 68px; top: 53px; width: 526px; height: 300px; background: var(--paper); }
  .card--navy  { left: 620px; top: 52px; width: 525px; height: 298px; background: var(--navy); }
  .card--white { left: 64px; top: 393px; width: 524px; height: 299px; background: var(--paper); border: 1px solid var(--edge); }
  .card--sky   { left: 620px; top: 393px; width: 525px; height: 299px; background: var(--sky); }

  .header-band { position: absolute; left: 0; top: 0; width: 526px; height: 160px; }

  .holder-name {
    position: absolute; right: 36px; top: 18px;
    color: var(--paper); font-weight: 700; font-size: 19px;
  }

  .wordmark {
    position: absolute;
    display: flex; align-items: center; gap: 12px;
    font-weight: 700; font-size: 44px; line-height: 1;
    color: var(--brand);
  }
  .wordmark__dot {
    width: 22px; height: 22px; border-radius: 50%;
    background: currentColor;
  }
  .wordmark--light { color: var(--paper); }
  .card--front .wordmark { left: 60px; top: 116px; }
  .card--navy .wordmark, .card--white .wordmark, .card--sky .wordmark {
    left: 0; right: 0; top: 118px; justify-content: center;
  }

  .website {
    position: absolute; left: 0; right: 0;
    text-align: center; font-size: 17px; letter-spacing: 4px;
  }
  .card--navy .website, .card--sky .website { top: 248px; color: var(--paper); }
  .card--white .website { top: 248px; color: var(--ink); }

  .details { position: absolute; font-size: 15px; line-height: 23px; }
  .details--left { left: 42px; top: 198px; }
  .details--right { left: 212px; top: 224px; }
  .details__label { color: var(--brand); }
  .details__row { display: flex; align-items: center; gap: 6px; }
  .details__row svg { width: 11px; height: 11px; fill: var(--brand); flex: none; }
  .details__divider {
    position: absolute; left: 193px; top: 230px;
    width: 1px; height: 36px; background: #8a8a8a;
  }
</style>
</head>
<body>

  <section class="card card--front" aria-label="Visittkort forside">
    <svg class="header-band" viewBox="0 0 526 160" aria-hidden="true">
      <path d="M0 0 H526 V132 C420 64 240 40 0 58 Z" fill="var(--navy)"/>
      <path d="M0 70 C200 46 400 70 526 146" fill="none" stroke="var(--stripe)" stroke-width="5"/>
      <path d="M0 82 C160 60 300 62 420 98" fill="none" stroke="var(--navy)" stroke-width="3"/>
    </svg>
    <div class="holder-name">Leif Brattvoll</div>
    <div class="wordmark"><span class="wordmark__dot"></span>Kjelvraket</div>

    <div class="details details--left">
      <div><span class="details__label">Org nr</span> 873 615 309</div>
      <div class="details__row">
        <svg viewBox="0 0 12 12"><path d="M6 1 L11 5.5 H9.5 V11 H2.5 V5.5 H1 Z"/></svg>8642 Raudvik
      </div>
      <div class="details__row">
        <svg viewBox="0 0 12 12"><path d="M3 1 L5 3.5 L4 5 C5 7 6 8 7.5 8.5 L9 7.5 L11 9.5 L9.5 11 C5 10.5 1.5 7 1 2.5 Z"/></svg>47382066
      </div>
    </div>
    <div class="details__divider"></div>
    <div class="details details--right">
      <div class="details__row">
        <svg viewBox="0 0 12 12"><path d="M1 4 L6 1 L11 4 V11 H1 Z M2 5 L6 8 L10 5 V10 H2 Z" fill-rule="evenodd"/></svg>Leif@fjordlast.no
      </div>
      <div class="details__row">
        <svg viewBox="0 0 12 12"><circle cx="6" cy="6" r="5" fill="none" stroke="var(--brand)" stroke-width="1.2"/><path d="M1 6 H11 M6 1 C3 4 3 8 6 11 M6 1 C9 4 9 8 6 11" fill="none" stroke="var(--brand)" stroke-width="1"/></svg>www.fjordlast.no
      </div>
    </div>
  </section>

  <section class="card card--navy" aria-label="Visittkort bakside, mørkeblå">
    <div class="wordmark wordmark--light"><span class="wordmark__dot"></span>Kjelvraket</div>
    <div class="website">www.fjordlast.no</div>
  </section>

  <section class="card card--white" aria-label="Visittkort bakside, hvit">
    <div class="wordmark"><span class="wordmark__dot"></span>Kjelvraket</div>
    <div class="website">www.fjordlast.no</div>
  </section>

  <section class="card card--sky" aria-label="Visittkort bakside, lyseblå">
    <div class="wordmark wordmark--light"><span class="wordmark__dot"></span>Kjelvraket</div>
    <div class="website">www.fjordlast.no</div>
  </section>

</body>
</html>
```